Professional and creative business card design for recruiting service providers

Our company supports German medium-sized companies in filling vacancies promptly. For this we use social media marketing and bring our customers into the visibility.

We want a professional but also creative design for our business cards.

Please look at lindqvar-staff.de to get an impression of our CI.

Target Market(s)

Small and medium-sized companies in Germany from the industry

Industry/Entity Type

Industrie, Handwerk

Contact Information for Business Card

Name, Position, Telefonnummer, Email, Website

Colors
EE7325
F08F49
F5BC92
FAE3D3
FDF4ED

Requirements
Must have
• A picture of the employee and in the style of www.lindqvar-staff.de

```html
<!DOCTYPE html>
<html lang="en">
<head>
<meta charset="utf-8">
<title>Lindqvar &amp; Staff – Business Card</title>
<link rel="stylesheet" href="https://fonts.googleapis.com/css2?family=Lato:wght@400;700;900&family=Oswald:wght@500&display=swap">
<style>
  :root {
    --page-bg: #2a2a2a;
    --card-bg: #111111;
    --accent: #f05a24;
    --text-light: #ffffff;
    --divider: #8a8a8a;
    --photo-top: #3a3a3c;
    --photo-bottom: #1c1c20;
  }
  * { box-sizing: border-box; margin: 0; padding: 0; }
  html, body {
    width: 1200px;
    height: 900px;
    overflow: hidden;
    background: var(--page-bg);
    font-family: "Lato", sans-serif;
  }
  .card-sheet {
    width: 1200px;
    height: 900px;
    display: flex;
    flex-direction: column;
    align-items: center;
    justify-content: center;
    gap: 40px;
  }
  .card {
    position: relative;
    width: 640px;
    height: 366px;
    background: var(--card-bg);
    overflow: hidden;
    box-shadow: 0 10px 28px rgba(0, 0, 0, 0.45);
  }
  .accent-band {
    position: absolute;
    left: 0;
    right: 0;
    bottom: 0;
    height: 14px;
    background: var(--accent);
  }

  /* Front */
  .brand {
    position: absolute;
    left: 58px;
    top: 168px;
    display: flex;
    align-items: center;
    gap: 22px;
  }
  .brand-mark {
    width: 58px;
    height: 58px;
    background: var(--accent);
  }
  .brand-name {
    color: var(--text-light);
    font-weight: 900;
    font-size: 30px;
    line-height: 1.1;
    letter-spacing: 4px;
    text-transform: uppercase;
  }
  .employee-photo {
    position: absolute;
    right: 40px;
    bottom: 14px;
    width: 230px;
    height: 300px;
    background: linear-gradient(180deg, var(--photo-top), var(--photo-bottom));
    border-radius: 110px 110px 0 0;
  }

  /* Back */
  .identity {
    position: absolute;
    left: 60px;
    top: 126px;
    width: 230px;
    text-align: right;
  }
  .person-name {
    font-family: "Oswald", sans-serif;
    font-weight: 500;
    font-size: 32px;
    line-height: 1;
    color: var(--accent);
    text-transform: uppercase;
    letter-spacing: -0.5px;
    white-space: nowrap;
  }
  .person-role {
    margin-top: 6px;
    font-size: 16px;
    color: var(--text-light);
    letter-spacing: 0.5px;
  }
  .info-divider {
    position: absolute;
    left: 310px;
    top: 120px;
    width: 1px;
    height: 86px;
    background: var(--divider);
  }
  .contact-list {
    position: absolute;
    left: 334px;
    top: 124px;
    list-style: none;
    display: flex;
    flex-direction: column;
    gap: 8px;
  }
  .contact-item {
    display: flex;
    align-items: center;
    gap: 10px;
    font-size: 17px;
    color: var(--text-light);
    letter-spacing: 0.4px;
    white-space: nowrap;
  }
  .contact-icon {
    width: 18px;
    height: 18px;
    flex: none;
  }
</style>
</head>
<body>
<main class="card-sheet">

  <section class="card card-front" aria-label="Card front">
    <div class="brand">
      <div class="brand-mark" aria-hidden="true"></div>
      <div class="brand-name">Lindqvar<br>&amp; Staff</div>
    </div>
    <div class="employee-photo" role="img" aria-label="Portrait photo of the employee in a dark blazer and turtleneck"></div>
    <div class="accent-band"></div>
  </section>

  <section class="card card-back" aria-label="Card back">
    <div class="identity">
      <h1 class="person-name">Jonas Falkner</h1>
      <p class="person-role">Managing Director</p>
    </div>
    <div class="info-divider"></div>
    <ul class="contact-list">
      <li class="contact-item">
        <svg class="contact-icon" viewBox="0 0 24 24" aria-hidden="true">
          <path fill="var(--accent)" d="M6.6 10.8c1.4 2.8 3.8 5.1 6.6 6.6l2.2-2.2c.3-.3.7-.4 1-.2 1.1.4 2.3.6 3.6.6.6 0 1 .4 1 1V20c0 .6-.4 1-1 1C10.6 21 3 13.4 3 4c0-.6.4-1 1-1h3.5c.6 0 1 .4 1 1 0 1.3.2 2.5.6 3.6.1.3 0 .7-.2 1z"/>
        </svg>
        <span>040-318 274 965</span>
      </li>
      <li class="contact-item">
        <svg class="contact-icon" viewBox="0 0 24 24" aria-hidden="true">
          <rect x="2" y="5" width="20" height="14" fill="var(--accent)"/>
          <path d="M2 5l10 8 10-8" fill="none" stroke="var(--card-bg)" stroke-width="1.8"/>
        </svg>
        <span>info@lindqvar-staff.de</span>
      </li>
      <li class="contact-item">
        <svg class="contact-icon" viewBox="0 0 24 24" aria-hidden="true">
          <g fill="none" stroke="var(--accent)" stroke-width="2">
            <circle cx="12" cy="12" r="9.5"/>
            <ellipse cx="12" cy="12" rx="4" ry="9.5"/>
            <path d="M2.5 12h19M4 7h16M4 17h16"/>
          </g>
        </svg>
        <span>www.lindqvar-staff.de</span>
      </li>
    </ul>
    <div class="accent-band"></div>
  </section>

</main>
</body>
</html>
```